COMPANY NAME: Bright Harbor Ventures: Task Description: We are a new UK based business with global rea

Target Market

- Personal and professional development – 30-55 age group, corporate leaders, Eastern European and Asian markets
- On-assignment projects – Corporate market – Eastern European and Asian Markets
- Property investment - 35-65 age group, Europe, USA, Australia

What we need

We need logos and brand design for a suite of web platforms (website, twitter and Facebook profile). We would like to have a cohesive and consistent look across all of our online platforms. The design suite must therefore include social media logos, backgrounds and headers. Specifically we are looking for:

a. Facebook header/page design: likely to have a more youthful look

b. Website: Header, background and layout that is responsive to devices, iPhone primarily, then tablet, then PC (we have purchased a website building package from SiteKettle so if you are familiar with one of their themes, it would be great to have a design that fits with a theme you would recommend); Design should be able to accommodate a place to position video in the medium term but an image in the short term.

c. LinkedIn: header/logo; more corporate look

d. Twitter: background/logo

e. Powerpoint template: background and logo - simple and soft background not busy

f. Electronic Newsletter: logo, header and sidebar; simple and soft background not busy

h. Business card: sophisticated and simple

Colors

We have in mind a preference for colors from the purple family, maybe lavender, so as to appeal to all genders and age groups. Though we are happy to go with a recommendation if you think otherwise.

We would like a look that is professional, airy, bright, fresh, futuristic, insightful, friendly.

Ethos of the brand

- experiencing opportunity and being fulfilled in a changing world
- services are facilitated through insights
- support provided through our product, services and tailored approach to coaching/partnerships (which includes private client match-making)
- we are service providers and passionate about quality and modern leadership skills at all stages in life.

The company name is "Bright Harbor Ventures” - our main message is helping people move to the next level - through investments, personal and professional growth.

Some of our messaging

1. International Leadership in a new world.

2. New technology;

3. Informed;

4. Positively Influential

5. Making a difference;

6. Empowered;

7. Risk free investments;

8. Commercial opportunity;

9. Fulfilled living;

10. Carefree and Fun Living;

11. Progression;

12. Open-minded

13. Energy/dynamic

The Business:
The business is to move people very quickly out of situations that hold them back. the situations could be their own personal situations; their career; their jobs; their teams; their ideas; their finances; their financial opportunities. Remove their fears and give them the strategies to take action. The team are international and have 40 years experience between them in this area.

We do want to come across modern and dynamic, customer outcome focussed, building long-term relationships; international.
Updates

Project Deadline Extended
Reason: We have not found the right designs - we are not just looking for a website design but also images and logos. Most images we can see in the designs are stock images - very standard. We need an image which will be the face of the company, like the shop front window. This main image will be used on social media (top image) and also the home page of the website.

Target Market(s)

30-55 years
Eastern Europe; UK; Asia; Africa; Middle East
Personal, Professional, Corporate, and Financial Growth

Industry/Entity Type

Business Service

Contact Information for Business Card

Simple and stylish
the 3 areas of the business on the reverse -

International look - Offices in UK and San Francisco

Company name
web address www.brightharborventure.com
email director@brightharborventure.com
Facebook bright harbor venture
LinkedIn Bright Harbor Venture
Twitter Bright Harbor Venture
Telephone: +44 (0) 768 213 5597

Logo Text

Something that symbolises unlimited growth - probably not text - could use the word INSIGHT in some way

Number of Pages Required

1 page

Colors
e4daeb
f3f1f8
ffffff

Requirements
Must have
• social media symbols and address
• company name
• Melanie Thorpe
• Director
• Telephone +44 (0) 768 213 5597
• Website name www.brightharborventure.co.uk
• Reverse of Card:
• Discreet, Fast, Bright Harbor Consultancy
• Corporate, Professional, Personal & Property Investment
Nice to have
• not too angular; soft lines; not too cluttered (possibly social media on the reverse and just logo, name, number on the front?
Should not have
• too busy

```html
<!DOCTYPE html>
<html lang="en">
<head>
<meta charset="utf-8">
<title>Bright Harbor Venture</title>
<link href="https://fonts.googleapis.com/css2?family=Merriweather:wght@300;400&display=swap" rel="stylesheet">
<style>
:root{
  --lavender:#e4daeb;
  --lavender-soft:#f3f1f8;
  --lavender-accent:#cbbbdc;
  --link:#a596b6;
  --ink:#454248;
  --ink-soft:#5d5a62;
  --white:#ffffff;
  --dark:#2d2c2f;
}
*{margin:0;padding:0;box-sizing:border-box}
html,body{width:1200px;height:2927px;overflow:hidden}
body{font-family:'Merriweather',Georgia,serif;font-weight:300;color:var(--ink);background:var(--white);position:relative}
.abs{position:absolute}
.logo{text-align:center;line-height:1;font-weight:400}
.logo .small{display:block;font-size:22px}
.logo .big{display:block;font-size:40px;margin-top:2px}

/* Hero */
.hero{position:absolute;left:0;top:0;width:1200px;height:576px;overflow:hidden}
.hero-photo{position:absolute;inset:0;background:radial-gradient(ellipse at 35% 40%,#8a7d72 0%,#5b524c 35%,#2f2b2a 75%,#1e1c1c 100%)}
.hero-shade{position:absolute;inset:0;background:rgba(20,18,20,.35)}
.hero .logo{left:210px;top:72px;color:var(--white);width:170px}
.menu-btn{left:944px;top:84px;width:55px;height:47px;background:var(--lavender);border-radius:2px}
.menu-btn span{position:absolute;left:22px;width:12px;height:2px;background:var(--white)}
.dropdown{left:792px;top:140px;width:207px;height:316px;background:var(--white);list-style:none;padding-top:18px}
.dropdown li{height:43.5px;font-size:14px;color:var(--link);padding-left:48px;position:relative}
.dropdown li::before{content:"›";position:absolute;left:20px;top:-2px;font-size:16px;color:#b8afc2}
.play{left:552px;top:260px}
.caption{left:0;width:1200px;top:406px;text-align:center;color:var(--white);font-size:24px;line-height:35px}
.dots{left:564px;top:519px;display:flex;gap:13px}
.dots i{width:8px;height:8px;border-radius:50%;background:var(--white)}
.dots i:first-child{background:rgba(255,255,255,.45)}

/* Welcome */
.welcome{position:absolute;left:0;top:576px;width:1200px;height:610px;overflow:hidden}
.welcome-photo{position:absolute;left:640px;top:0;width:560px;height:610px;background:linear-gradient(90deg,#fff 0%,#e9e7e8 30%,#c9c5c4 60%,#a9a3a1 100%)}
.welcome h1{left:195px;top:60px;width:620px;font-weight:300;font-size:41px;line-height:53px;color:var(--ink)}
.welcome h1 em{font-style:normal;color:var(--lavender-accent)}
.welcome p{left:201px;width:585px;font-size:14.3px;line-height:22.5px;color:var(--ink)}
.welcome p.lead{font-size:18px;line-height:28px}

/* Assignment */
.section-title{left:0;width:1200px;text-align:center;font-weight:300;font-size:43px;color:var(--ink)}
.tabs{left:190px;top:1364px;width:259px;list-style:none}
.tabs li{height:72.5px;line-height:56px;padding-left:42px;font-size:14.3px;color:var(--ink)}
.tabs li.active{border:1px solid #d6d3d8;height:56px;position:relative;margin-bottom:16.5px}
.tabs li.active::after{content:"";position:absolute;right:-9px;top:19px;width:16px;height:16px;background:#fff;border-right:1px solid #d6d3d8;border-top:1px solid #d6d3d8;transform:rotate(45deg)}
.tab-copy{left:474px;width:531px;font-size:14.3px;line-height:22.5px;color:var(--ink)}

/* Property */
.property{position:absolute;left:0;top:1662px;width:1200px;height:494px;background:var(--lavender)}
.property .sub{left:0;width:1200px;top:144px;text-align:center;font-size:14.3px;color:var(--ink-soft)}
.feature{top:232px;width:270px}
.feature .icon{position:absolute;left:0;top:0;width:58px;height:52px;background:#4b4a4e;display:flex;align-items:center;justify-content:center}
.feature h3{position:absolute;left:71px;top:0;font-weight:300;font-size:25px;line-height:28px;white-space:nowrap;color:var(--ink)}
.feature h4{position:absolute;left:71px;top:32px;font-weight:300;font-size:10.5px;color:var(--ink-soft)}
.feature p{position:absolute;left:0;top:74px;width:262px;font-size:9.8px;line-height:17.5px;color:var(--ink-soft)}

/* Contact */
.contact{position:absolute;left:0;top:2156px;width:1200px;height:497px;overflow:hidden}
.contact-photo{position:absolute;inset:0;background:linear-gradient(160deg,#3a393b 0%,#555357 45%,#3d3c3f 75%,#2a292b 100%)}
.contact .kicker{left:0;width:1200px;top:106px;text-align:center;color:#e6e3e8;font-size:18.5px}
.contact h2{left:0;width:1200px;top:137px;text-align:center;color:var(--white);font-weight:300;font-size:37px}
.contact .row{color:var(--white);font-size:19px;line-height:28px}
.contact svg{position:absolute}

/* Footer */
.site-footer .logo{left:450px;top:2717px;width:300px;color:var(--ink)}
.foot-links{left:0;width:1200px;top:2808px;text-align:center;font-size:14px;color:var(--link)}
.foot-links span{margin:0 11px}
.copyright{left:0;width:1200px;top:2858px;text-align:center;font-size:13px;color:var(--link)}
</style>
</head>
<body>

<header class="hero">
  <div class="hero-photo" role="img" aria-label="Photograph of two business people in conversation at a meeting table"></div>
  <div class="hero-shade"></div>
  <div class="logo abs"><span class="small">Bright Harbor</span><span class="big">Venture</span></div>
  <div class="menu-btn abs"><span style="top:18px"></span><span style="top:22px"></span><span style="top:26px"></span></div>
  <svg class="play abs" width="96" height="96" viewBox="0 0 96 96"><circle cx="48" cy="48" r="47" fill="rgba(255,255,255,.28)"/><path d="M38 30 L66 48 L38 66 Z" fill="#2c2a2c" opacity=".75"/></svg>
  <p class="caption abs">Lorem ipsum dolor sit amet, consectetur adipiscing elit,<br>sed do eiusmod tempor incididunt ut labore</p>
  <div class="dots abs"><i></i><i></i><i></i><i></i></div>
  <ul class="dropdown abs">
    <li>About You</li><li>About Us</li><li>Our Values</li><li>Testimonials</li><li>Social Media</li><li>News Alert</li>
  </ul>
</header>

<section class="welcome">
  <div class="welcome-photo" role="img" aria-label="Photograph of two colleagues reviewing a tablet together"></div>
  <h1 class="abs"><em>Hello</em> and welcome to the company that works with you on your terms.</h1>
  <p class="abs" style="top:262px">If you seek an experienced and trusted partner to work with you on an assignment or simply want some strategies to move your personal or professional talents to the next level then you are in the right place.</p>
  <p class="abs" style="top:350px">If you feel that the pace of change in business is so fast that to be anoutstanding leader you should ensure you are brought up to speed regularly then you are in the right place.If you are hearing about the essential new leadership essentials and you are ready to hear how to adopt them into your life or business then you are at the right place.</p>
  <p class="abs lead" style="top:484px">I am so convinced that you will be delighted with how fast you can make change happen.</p>
</section>

<section class="assignment">
  <h2 class="section-title abs" style="top:1265px">On Assignment</h2>
  <ul class="tabs abs">
    <li class="active">Team Cohesion Strategy</li>
    <li>Go To Market Strategy</li>
    <li>Internationalisation Strategy</li>
  </ul>
  <p class="tab-copy abs" style="top:1357px">Sed ut perspiciatis unde omnis iste natus error sit voluptatem accusantium doloremque laudantium, totam rem aperiam, eaque ipsa quae ab illo inventore veritatis et quasi architecto beatae vitae dicta sunt explicabo. Nemo enim ipsam voluptatem quia voluptas sit aspernatur aut odit aut fugit, sed quia consequuntur magni dolores eos qui</p>
  <p class="tab-copy abs" style="top:1493px">Ratione voluptatem sequi nesciunt. Neque porro quisquam est, qui dolorem ipsum quia dolor sit amet, consectetur, adipisci velit, sed quia non numquam eius modi tempora incidunt</p>
</section>

<section class="property">
  <h2 class="section-title abs" style="top:68px">Property</h2>
  <p class="sub abs">Private Client &nbsp;| &nbsp;Promotion and cash-buyer matching</p>
  <div class="feature abs" style="left:201px">
    <div class="icon"><svg width="32" height="26" viewBox="0 0 32 26" fill="none" stroke="#fff" stroke-width="1.6"><ellipse cx="16" cy="14" rx="11" ry="8"/><path d="M9 20v4M22 20v4M27 12h3M13 6h6"/><circle cx="21" cy="12" r="1" fill="#fff"/></svg></div>
    <h3>Investment</h3><h4>High Return Projects</h4>
    <p>Sed ut perspiciatis unde omnis iste natus error sit voluptatem accusantium doloremque laudantium, totam rem aperiam, eaque ipsa quae ab illo inventore veritatis et quasi architecto beatae vitae</p>
  </div>
  <div class="feature abs" style="left:476px">
    <div class="icon"><svg width="28" height="28" viewBox="0 0 28 28" fill="none" stroke="#fff" stroke-width="1.6"><path d="M8 3h12v8a6 6 0 0 1-12 0z"/><path d="M8 6H3a5 5 0 0 0 5 6M20 6h5a5 5 0 0 1-5 6M14 17v5M9 25h10"/></svg></div>
    <h3>Commercial</h3><h4>High Return Projects</h4>
    <p>Sed ut perspiciatis unde omnis iste natus error sit voluptatem accusantium doloremque laudantium, totam rem aperiam, eaque ipsa quae ab illo inventore veritatis et quasi architecto beatae</p>
  </div>
  <div class="feature abs" style="left:749px">
    <div class="icon"><svg width="30" height="30" viewBox="0 0 30 30" fill="none" stroke="#fff" stroke-width="1.6"><circle cx="15" cy="15" r="12"/><path d="M15 7v8h6"/></svg></div>
    <h3>Prestige Residential</h3><h4>US, Australia, UK</h4>
    <p>Sed ut perspiciatis unde omnis iste natus error sit voluptatem accusantium doloremque laudantium, totam rem aperiam, eaque ipsa quae ab illo inventore veritatis et quasi architecto beatae</p>
  </div>
</section>

<section class="contact">
  <div class="contact-photo" role="img" aria-label="Monochrome photograph of hands signing documents on a desk"></div>
  <p class="kicker abs">Let’s chat, if you want a non committal conversation</p>
  <h2 class="abs">Get in touch by E-mail or Telephone</h2>
  <svg style="left:232px;top:245px" width="26" height="20" viewBox="0 0 26 20" fill="none" stroke="#fff" stroke-width="1.8"><rect x="4" y="2" width="18" height="12"/><path d="M1 17h24"/></svg>
  <p class="row abs" style="left:280px;top:240px">Director@brightharborventure.com</p>
  <svg style="left:232px;top:292px" width="24" height="26" viewBox="0 0 24 26" fill="none" stroke="#fff" stroke-width="1.8"><rect x="2" y="6" width="20" height="18"/><rect x="6" y="2" width="8" height="8"/><path d="M7 15h2M11 15h2M15 15h2M7 19h2M11 19h2M15 19h2"/></svg>
  <p class="row abs" style="left:280px;top:290px">+44 (0) 768 213 5597</p>
  <svg style="left:660px;top:243px" width="26" height="20" viewBox="0 0 26 20" fill="none" stroke="#fff" stroke-width="1.8"><rect x="1" y="1" width="24" height="18"/><circle cx="8" cy="8" r="2.5"/><path d="M4 15c1-3 7-3 8 0M15 7h7M15 11h7"/></svg>
  <p class="row abs" style="left:714px;top:240px">Bright Harbor Venture Limited,<br>registered in England and Wales.</p>
  <p class="row abs" style="left:714px;top:324px">Registeres number 10582914.</p>
</section>

<footer class="site-footer">
  <div class="logo abs"><span class="small">Bright Harbor</span><span class="big">Venture</span></div>
  <p class="foot-links abs">About You<span>|</span>About Us<span>|</span>Our Values<span>|</span>Testimonials<span>|</span>Social Media<span>|</span>News Alert</p>
  <p class="copyright abs">© 2016 Company Name &nbsp;| All Rights Reserved</p>
</footer>

</body>
</html>
```